Accountant website

Please design a accountant website for www.fenwaybridgeadvisory.com.au. This site is majorly out of date, and is not supported by modern browsers.

The style should use the reds from the design at dev.fenwaybridgeadvisory.com.au, and should be modern and make use of Slides (large content slides that the user scrolls through on the front page).

The content is largely already on the site, however happy to move some around to suit the modern design as required.

The dev.fenwaybridgeadvisory.com.au was a rough mock up that I have completed that the client is "happy" with the direction, however this needs a lot of polish and finishing touches, and I will accept designs that differ from this, but highly recommend that this is used as a guide.

Ready to be sliced PSD Only - HTML no required.

In all honesty, although I can technically do a lot of this, the polished finished I want for this site has eluded me in a few attempts, and therefore I am looking out there at you much more artistic people to finish (or redesign if required) this site.

Target Market(s)

Higher end Small - Medium Business

Industry/Entity Type

Accountant

Requirements
Must have
• Must use the logo from dev.fenwaybridgeadvisory.com.au use exactly the red colours as defined in this layout. A basic layout PSD (to get the colour etc) and the logo in ai format is attached to this project. Please ignore the SSL warning on the development site.

The final product does NOT have to be the same as shown on dev.fenwaybridgeadvisory.com.au however the red colour scheme must be used. The client DOES want the logo on the RIGHT.

Must have a front landing page design, and a page layout that considers the other page content (at least one separate PSD)
Nice to have
• I really am looking at a slide format for the front page simular to:

http://www.quillo.com/au/
http://www.vaultmoor.com/

The attached photos should be used on the site. Was considering a rotating banner with these images are a watermark background on a solid Red header bar, but happy to be shown other options.
Should not have
• Please no "Layout Goblin" submissions.

```html
<!DOCTYPE html>
<html lang="en">
<head>
<meta charset="utf-8">
<title>Fenway Bridge Advisory</title>
<link href="https://fonts.googleapis.com/css2?family=Roboto:wght@300;400;500;700&display=swap" rel="stylesheet">
<style>
:root{
  --red:#d12027;
  --red-dark:#b71c22;
  --ink:#222;
  --body:#444;
  --grey-band:#efefef;
  --footer:#1d1d1d;
  --white:#fff;
}
*{margin:0;padding:0;box-sizing:border-box}
html,body{width:905px;height:1200px;overflow:hidden;background:var(--white)}
body{position:relative;font-family:'Roboto',sans-serif;color:var(--body)}
a{color:inherit;text-decoration:none}

.site-header{position:absolute;left:0;top:0;width:905px;height:102px;border-bottom:1px solid #e3b9bb}
.brand{position:absolute;left:88px;top:24px;display:flex;align-items:center;gap:10px}
.brand-mark{width:22px;height:22px;background:var(--red)}
.brand-name{font-size:23px;font-weight:700;color:var(--ink);line-height:1;letter-spacing:.5px}
.call{position:absolute;right:90px;top:15px;text-align:left;color:#444}
.call-label{font-size:13px;margin-left:24px}
.call-number{display:flex;align-items:center;gap:6px;font-size:16px;margin-top:2px}
.main-nav{position:absolute;right:89px;top:70px;display:flex;gap:15px;font-size:12px;font-weight:500;color:#333}
.main-nav .active{color:var(--red)}

.hero{position:absolute;left:0;top:102px;width:905px;height:372px;background:linear-gradient(90deg,#c9c3bf 0%,#b8322f 28%,#c5262a 55%,#b33 70%,#cfcac6 100%)}
.hero-dots{position:absolute;left:400px;top:273px;display:flex;gap:5px}
.hero-dots span{width:11px;height:11px;border-radius:50%;background:var(--white)}
.hero-caption{position:absolute;left:0;bottom:0;width:905px;height:81px;background:rgba(60,60,60,.72);color:var(--white);text-align:center}
.hero-title{font-size:37px;font-weight:300;line-height:1;margin-top:5px}
.hero-sub{font-size:26px;font-weight:300;line-height:1;margin-top:5px}

.intro{position:absolute;left:86px;top:514px;width:446px}
.section-title{font-size:15px;font-weight:500;color:var(--ink);text-transform:uppercase;line-height:1.2}
.section-title em{font-style:normal;color:var(--red)}
.intro p{font-size:10px;line-height:14px;letter-spacing:.2px;margin:8px 0 27px}
.intro-photo{position:absolute;left:550px;top:496px;width:262px;height:207px;border:3px solid #8f8f8f;background:linear-gradient(180deg,#b7c1c8 0%,#4b6f93 45%,#3b5a80 70%,#6c5b4a 100%)}

.features{position:absolute;left:0;top:727px;width:905px;height:263px;background:var(--grey-band)}
.feature{position:absolute;width:310px}
.feature-icon{position:absolute;left:0;top:0;width:86px;height:86px;border-radius:50%;border:4px solid #111;background:radial-gradient(circle at 50% 40%,#fff 0%,#e4e4e4 100%);display:flex;align-items:center;justify-content:center}
.feature-body{position:absolute;left:97px;top:7px;width:210px}
.feature-body h3{font-size:14px;font-weight:500;color:var(--ink);text-transform:uppercase;line-height:1.1}
.feature-body h3 em{font-style:normal;color:var(--red)}
.feature-body p{font-size:10px;line-height:13px;margin-top:4px}
.feature-body .more{display:block;font-size:10px;color:var(--red);margin-top:4px}

.site-footer{position:absolute;left:0;top:990px;width:905px;height:180px;background:var(--footer);color:#ddd}
.footer-col h4{font-size:12px;font-weight:500;color:var(--white);margin-bottom:10px}
.quick-links{position:absolute;left:93px;top:20px}
.quick-links li{list-style:none;font-size:9.5px;line-height:20.8px}
.testimonial{position:absolute;left:254px;top:20px;width:152px}
.testimonial blockquote{font-size:9.5px;line-height:12.5px;letter-spacing:.3px}
.testimonial cite{display:block;text-align:right;font-style:normal;font-size:8.5px;margin-top:7px;letter-spacing:.5px}
.btn{display:inline-block;background:var(--red);color:var(--white);font-size:10.5px;padding:3px 6px;border-radius:1px}
.testimonial .btn{position:absolute;right:3px;top:110px}
.contact{position:absolute;left:449px;top:20px;width:135px}
.contact .field{height:16px;background:var(--white);border:1px solid #bbb;font-size:8px;font-style:italic;color:#999;padding:2px 6px;margin-bottom:4px}
.contact .field.msg{height:32px}
.contact .btn{position:absolute;right:0;top:139px}
.partner-badge{position:absolute;left:630px;top:18px;width:186px;height:52px;border-radius:26px;background:#3a3a3a}
.footer-brand{position:absolute;left:633px;top:102px;display:flex;align-items:center;gap:8px}
.footer-brand .brand-mark{background:#cfcfcf}
.footer-brand .brand-name{color:#cfcfcf;font-size:22px}

.bottom-bar{position:absolute;left:0;top:1170px;width:905px;height:30px;background:var(--red);color:var(--white)}
.copyright{position:absolute;left:93px;top:9px;font-size:9.5px}
.follow{position:absolute;right:89px;top:5px;display:flex;align-items:center;gap:5px;font-size:12px;font-weight:500}
.follow .social{width:18px;height:18px;border-radius:50%;background:var(--white)}
.follow .label{margin-right:5px}
</style>
</head>
<body>

<header class="site-header">
  <div class="brand"><span class="brand-mark"></span><span class="brand-name">FENWAY BRIDGE</span></div>
  <div class="call">
    <div class="call-label">Call Us Today</div>
    <div class="call-number">
      <svg width="18" height="18" viewBox="0 0 18 18"><circle cx="9" cy="9" r="8" fill="none" stroke="#d12027" stroke-width="1.4"/><path d="M6 5.5c.6-.6 1.2-.4 1.5.2l.6 1.2c.2.4 0 .8-.3 1l-.5.4c.5 1 1.3 1.8 2.3 2.3l.4-.5c.3-.3.7-.5 1-.3l1.2.6c.6.3.8.9.2 1.5-1 1-2.6.8-4.3-.9S5 6.5 6 5.5z" fill="#d12027"/></svg>
      012-555-0142
    </div>
  </div>
  <nav class="main-nav">
    <a class="active">About Us</a><a>Services</a><a>Working With Us</a><a>Testimonials</a><a>Article Of The Moment</a><a>Client Login</a>
  </nav>
</header>

<section class="hero" role="img" aria-label="Photo of four smiling team members seated in front of a red office wall bearing the firm's sign">
  <div class="hero-dots"><span></span><span></span><span></span><span></span></div>
  <div class="hero-caption">
    <div class="hero-title">Business can be hard</div>
    <div class="hero-sub">But We Make detailed analysis of your finances easy</div>
  </div>
</section>

<section class="intro">
  <h2 class="section-title"><em>Getting to know</em> Fenway Bridge Advisory</h2>
  <p>Fenway Bridge Advisory aims to service the needs of its clients by focusing on the present rather than reporting on historical figures. We recognise that business owners benefit from regular contact with their accountant. One who undertakes a hands on approach in working with business owners to improve their business.</p>
  <h2 class="section-title"><em>Fenway Bridge</em> Advisory Difference</h2>
  <p>Not all Accountants are created equally … the Fenway Bridge Advisory difference. Fenway Bridge Advisory takes pride in not following the status quo, the following points are just some of the unique benefits you will experience when working with us.</p>
</section>
<div class="intro-photo" role="img" aria-label="Photo of an advisor in a red dress sitting on a wooden jetty by the river with office buildings behind"></div>

<section class="features">
  <div class="feature" style="left:89px;top:25px">
    <div class="feature-icon"><svg width="50" height="34" viewBox="0 0 50 34"><rect x="3" y="8" width="26" height="18" rx="9" fill="none" stroke="#d12027" stroke-width="6"/><rect x="21" y="8" width="26" height="18" rx="9" fill="none" stroke="#d12027" stroke-width="6"/></svg></div>
    <div class="feature-body"><h3><em>Believing in the</em> here and now</h3><p>There are many varlations of passages of lorem Ipsum avallable, but the majorlty have alteration in some form.</p><a class="more">Read More [+]</a></div>
  </div>
  <div class="feature" style="left:475px;top:25px">
    <div class="feature-icon"><svg width="56" height="46" viewBox="0 0 56 46"><path d="M4 24L28 4l24 20" fill="none" stroke="#d12027" stroke-width="4"/><path d="M12 20v24M44 20v24" stroke="#d12027" stroke-width="3"/></svg></div>
    <div class="feature-body"><h3><em>Your place,</em> in your time</h3><p>There are many varlations of passages of lorem Ipsum avallable, but the majorlty have alteration in some form.</p><a class="more">Read More [+]</a></div>
  </div>
  <div class="feature" style="left:89px;top:150px">
    <div class="feature-icon"><svg width="46" height="40" viewBox="0 0 46 40"><rect x="3" y="10" width="32" height="27" fill="none" stroke="#d12027" stroke-width="3"/><path d="M9 20h14M9 26h20M9 31h20" stroke="#d12027" stroke-width="2"/><path d="M22 22L40 4l4 4-18 18-6 2z" fill="#d12027"/></svg></div>
    <div class="feature-body"><h3><em>Monthly</em> billing</h3><p>There are many varlations of passages of lorem Ipsum avallable, but majorlty have alteration in some.</p><a class="more">Read More [+]</a></div>
  </div>
  <div class="feature" style="left:475px;top:150px">
    <div class="feature-icon"><svg width="48" height="48" viewBox="0 0 48 48"><path d="M10 14A18 18 0 1 1 8 32" fill="none" stroke="#d12027" stroke-width="4"/><path d="M4 10l8 2-2 8z" fill="#d12027"/><path d="M24 12v13h9" fill="none" stroke="#d12027" stroke-width="4"/></svg></div>
    <div class="feature-body"><h3><em>We will actually</em> call you back</h3><p>There are many varlations of passages of lorem Ipsum avallable, but majorlty have alteration..</p><a class="more">Read More [+]</a></div>
  </div>
</section>

<footer class="site-footer">
  <div class="footer-col quick-links"><h4>Quick Links</h4>
    <ul><li>&gt; About Us</li><li>&gt; Services</li><li>&gt; Working With Us</li><li>&gt; Testimonials</li><li>&gt; Article Of The Moment</li><li>&gt; Client Login</li></ul>
  </div>
  <div class="footer-col testimonial"><h4>Testimonials</h4>
    <blockquote>“ Lorem ipsum dolor sit amet tetuer adipiscing elit, sed diam nonum sum ipsum Lorem ipsum dolor sit amet, tetuer adipiscing elit, sed diam nonum ”</blockquote>
    <cite>Lorem, Director</cite>
    <a class="btn">View All »</a>
  </div>
  <div class="footer-col contact"><h4>Quick Contact</h4>
    <div class="field">Enter Your Name</div><div class="field">Enter Your Email</div><div class="field">Enter Your Phone</div><div class="field msg">Message</div>
    <a class="btn">Send Message »</a>
  </div>
  <div class="partner-badge"></div>
  <div class="footer-brand"><span class="brand-mark"></span><span class="brand-name">FENWAY BRIDGE</span></div>
</footer>

<div class="bottom-bar">
  <div class="copyright">© 2013 Fenway Bridge Advisory. All Rights Reserved.</div>
  <div class="follow"><span class="label">Follow Us On:</span><span class="social"></span><span class="social"></span><span class="social"></span></div>
</div>

</body>
</html>
```